The Linen Loft Co

We need a business card design for our wardrobe company.
Please visit our website www.gentlelinenlofts.com to get an idea of who we are.

```html
<!DOCTYPE html>
<html lang="en">
<head>
<meta charset="utf-8">
<title>The Linen Loft Co — Business Card</title>
<link rel="stylesheet" href="https://fonts.googleapis.com/css2?family=Jost:wght@400;500;600&display=swap">
<style>
  :root {
    --backdrop: #dcdcdc;
    --card-dark: #0a0a0a;
    --card-light: #ffffff;
    --gold: #c08a1a;
    --muted: #bdbdbd;
    --light-text: #f2f2f2;
    --ink: #111111;
  }
  * { margin: 0; padding: 0; box-sizing: border-box; }
  html, body {
    width: 1125px;
    height: 1200px;
    overflow: hidden;
    background: var(--backdrop);
    font-family: "Jost", sans-serif;
  }
  .card {
    position: absolute;
    left: 150px;
    width: 825px;
    height: 471px;
  }
  .card-front { top: 98px; background: var(--card-dark); }
  .card-back { top: 631px; background: var(--card-light); }

  .holder {
    position: absolute;
    right: 463px;
    top: 208px;
    text-align: right;
  }
  .holder-name {
    color: var(--gold);
    font-size: 31px;
    font-weight: 400;
    line-height: 1.1;
    white-space: nowrap;
  }
  .holder-role {
    color: var(--muted);
    font-size: 20px;
    line-height: 1.2;
  }

  .contact {
    position: absolute;
    left: 406px;
    top: 173px;
    color: var(--light-text);
    font-size: 20px;
    line-height: 25px;
  }
  .address { margin-bottom: 20px; }
  .contact-line {
    display: flex;
    align-items: center;
    gap: 8px;
  }
  .contact-line svg { width: 17px; height: 17px; flex: none; }

  .brand-mark {
    position: absolute;
    left: 236px;
    top: 218px;
    width: 44px;
    height: 44px;
    background: var(--ink);
  }
  .brand-text {
    position: absolute;
    left: 340px;
    top: 204px;
    width: 360px;
    text-align: center;
    color: var(--ink);
  }
  .brand-name {
    font-size: 27px;
    font-weight: 600;
    letter-spacing: 0.4px;
    line-height: 36px;
    white-space: nowrap;
  }
  .brand-tagline {
    font-size: 22px;
    font-weight: 500;
    line-height: 36px;
    white-space: nowrap;
  }
</style>
</head>
<body>
  <section class="card card-front">
    <div class="holder">
      <div class="holder-name">Daniel Hartley</div>
      <div class="holder-role">President</div>
    </div>
    <div class="contact">
      <div class="address">
        <div>Marlow House, 42 Fenwick Street</div>
        <div>London E2 7QT</div>
      </div>
      <div class="contact-line">
        <svg viewBox="0 0 24 24" aria-hidden="true"><path fill="#f2f2f2" d="M6.6 10.8c1.4 2.8 3.8 5.1 6.6 6.6l2.2-2.2c.3-.3.7-.4 1-.2 1.1.4 2.3.6 3.6.6.6 0 1 .4 1 1V20c0 .6-.4 1-1 1C10.6 21 3 13.4 3 4c0-.6.4-1 1-1h3.5c.6 0 1 .4 1 1 0 1.3.2 2.5.6 3.6.1.3 0 .7-.2 1z"/></svg>
        <span>020 7946 0183</span>
      </div>
      <div class="contact-line">
        <svg viewBox="0 0 24 24" aria-hidden="true"><rect x="3" y="6" width="18" height="12" fill="none" stroke="#f2f2f2" stroke-width="2"/><path d="M3 6l9 7 9-7" fill="none" stroke="#f2f2f2" stroke-width="2"/></svg>
        <span>info@gentlelinenlofts.com</span>
      </div>
      <div class="contact-line">
        <svg viewBox="0 0 24 24" aria-hidden="true"><circle cx="12" cy="12" r="9" fill="none" stroke="#f2f2f2" stroke-width="2"/><path d="M3 12h18M12 3c3 3 3 15 0 18M12 3c-3 3-3 15 0 18" fill="none" stroke="#f2f2f2" stroke-width="1.6"/></svg>
        <span>www.gentlelinenlofts.com</span>
      </div>
    </div>
  </section>

  <section class="card card-back">
    <div class="brand-mark"></div>
    <div class="brand-text">
      <div class="brand-name">THE LINEN LOFT CO</div>
      <div class="brand-tagline">Tailored to Every Room</div>
    </div>
  </section>
</body>
</html>
```